Brookvale Building Company - advertisement poster

I am looking to print some canvas signs to advertise my general contracting company, Brookvale Building Company. The sign will measure 6' long x 3' high so the size should match that ratio. I already have a logo icon, which is the Letter 'B' and some trees that I would like to incorporate, see attached. I would also like the to have the following information listed:
1) phone number: 831-555-0172
2) email: brookvalebuildingcompany@mailnest.example
3) website: brookvalebuildingcompany.example
4) Lic#4826130
5) I want to use this text: "BUILD WITH THE B-CREW!"

The ad should be relatively simple and clean. Black and Green are my company colors. I am open to creative ideas!

Target Market(s)

People looking to renovate their homes

Industry/Entity Type

Construction

Colors
59FF00
82FF00
B8FF75
E3FFCB
F4FFEA

Requirements
Must have
• Must have my company logo
Should not have
• No photos or complex graphics

```html
<!DOCTYPE html>
<html lang="en">
<head>
<meta charset="utf-8">
<title>Brookvale Building Company – Sign</title>
<link rel="stylesheet" href="https://fonts.googleapis.com/css2?family=Krona+One&family=Archivo+Black&family=Poppins:wght@600;700&display=swap">
<style>
  :root {
    --green: #6cb33f;
    --black: #000000;
    --white: #ffffff;
    --backdrop: #979797;
    --ink: #111111;
  }
  html, body {
    margin: 0;
    padding: 0;
    width: 1200px;
    height: 865px;
    overflow: hidden;
    background: var(--backdrop);
  }
  .sign {
    position: absolute;
    left: 0;
    top: 132px;
    width: 1200px;
    height: 600px;
    display: block;
  }
  .headline { font-family: "Krona One", "Archivo Black", sans-serif; }
  .brand-name { font-family: "Krona One", sans-serif; fill: var(--white); }
  .phone-number { font-family: "Archivo Black", sans-serif; fill: var(--white); }
  .license { font-family: "Poppins", sans-serif; font-weight: 700; }
  .contact-line { font-family: "Poppins", sans-serif; font-weight: 600; fill: var(--ink); font-size: 27px; }
</style>
</head>
<body>
<svg class="sign" viewBox="0 0 1200 600" xmlns="http://www.w3.org/2000/svg">
  <!-- panels -->
  <rect class="panel-top" x="0" y="0" width="1200" height="376" fill="var(--black)"/>
  <rect class="panel-bottom" x="0" y="376" width="1200" height="224" fill="var(--white)"/>

  <!-- company name -->
  <g class="brand">
    <rect x="205" y="70" width="72" height="72" fill="var(--green)"/>
    <text class="brand-name" x="241" y="212" font-size="36" text-anchor="middle" textLength="372" lengthAdjust="spacingAndGlyphs">BROOKVALE</text>
    <text class="brand-name" x="241" y="262" font-size="19" text-anchor="middle" textLength="372" lengthAdjust="spacingAndGlyphs">BUILDING COMPANY</text>
  </g>

  <!-- headline -->
  <g class="headline">
    <text x="486" y="201" font-size="150" fill="var(--white)" textLength="606" lengthAdjust="spacingAndGlyphs">BUILD</text>
    <rect x="1104" y="96" width="38" height="105" fill="var(--green)"/>
    <text x="0" y="0" font-size="24" fill="var(--white)" transform="translate(1132 196) rotate(-90)" textLength="94" lengthAdjust="spacingAndGlyphs">WITH</text>
    <text x="488" y="285" font-size="80" fill="var(--white)" textLength="220" lengthAdjust="spacingAndGlyphs">THE</text>
    <text x="736" y="285" font-size="80" fill="var(--green)" textLength="406" lengthAdjust="spacingAndGlyphs">B-CREW</text>
  </g>

  <!-- phone bar -->
  <g class="phone-bar">
    <rect x="48" y="318" width="1107" height="116" rx="9" fill="var(--white)"/>
    <rect x="52" y="322" width="1099" height="108" rx="7" fill="var(--green)"/>
    <circle cx="128" cy="376" r="36" fill="var(--white)"/>
    <path d="M112 354c3-2 6-1 7 2l4 9c1 2 0 4-2 5l-3 2c2 6 7 11 13 14l2-3c1-2 3-3 5-2l9 4c3 1 4 4 2 7l-3 4c-3 3-8 3-13 1-12-6-21-15-26-27-2-5-2-10 1-13z" fill="var(--green)"/>
    <path d="M132 350a18 18 0 0 1 16 16M132 358a10 10 0 0 1 8 8" fill="none" stroke="var(--green)" stroke-width="3" stroke-linecap="round"/>
    <text class="phone-number" x="185" y="410" font-size="90" textLength="890" lengthAdjust="spacingAndGlyphs">831-555-0172</text>
  </g>

  <!-- license -->
  <g class="license">
    <rect x="47" y="465" width="418" height="74" rx="7" fill="var(--black)" stroke="var(--black)" stroke-width="2"/>
    <path d="M54 466h108v72H54a6 6 0 0 1-6-6V472a6 6 0 0 1 6-6z" fill="var(--white)"/>
    <text x="105" y="518" font-size="44" fill="var(--ink)" text-anchor="middle">LIC</text>
    <text x="182" y="518" font-size="46" fill="var(--white)" textLength="262" lengthAdjust="spacingAndGlyphs">#4826130</text>
  </g>

  <!-- contacts -->
  <g class="contacts">
    <rect x="504" y="472" width="30" height="20" fill="var(--green)"/>
    <path d="M504 472l15 11 15-11" fill="none" stroke="var(--white)" stroke-width="2"/>
    <text class="contact-line" x="548" y="492" textLength="604" lengthAdjust="spacingAndGlyphs">brookvalebuildingcompany@mailnest.example</text>

    <circle cx="519" cy="530" r="14" fill="none" stroke="var(--green)" stroke-width="3"/>
    <ellipse cx="519" cy="530" rx="6" ry="14" fill="none" stroke="var(--green)" stroke-width="2"/>
    <path d="M505 530h28M508 522h22M508 538h22" stroke="var(--green)" stroke-width="2"/>
    <text class="contact-line" x="550" y="540" textLength="470" lengthAdjust="spacingAndGlyphs">brookvalebuildingcompany.example</text>
  </g>
</svg>
</body>
</html>
```